Tea standup pouch labels

Dear designers,
I need a minimalistic and modern label for my loose tea stand-up pouches (100, 250 and 500gm packs). The label should cover 70-80% of the pouch face (front and rear both).
The label will be 2 part label - Front and Rear side labels.
The labels should have a green background (Pantone Green C) with Golden or White or black colour text. Please either use the Golden logo or black logo to see which looks good with Pantone Green C background.
I am also attaching the content file and a few other files (Assam tea logo) to be used in the label.
The Assam tea logo should be small at the bottom left or right side of the front side. The logo should be dominant on the front page (some of the designs I received have small logo and big "100% single estate tea" and "Assam logo" as big characters on the front page which is not what I am looking for.

The font style should note simple Times new roman or Arial. It should look modern and should be something matching to the logo sentence 'Freshest possible' but should also not be in italics. Please refer to files Font style reference front and back for the style of font. Also use the same box space design on the rear - Content should be in White background; the rectangular box edges should be rounded and the border should be in dual colour - Golden and white or in black and white depending on the logo colour used (golden or black).

For the Rear page - headings could be in Golden colour or black colour depending on the logo colour you choose to use and the text can be in white colour i.e. Option 1 - Headings in golden colour and text in white colour; Option 2 - Heading in Black colour and text in white colour or any other combination that looks good - designer to decide.

Please let me know if you need any further information.

thanks,
Rotek

33b8a4

```html
<!DOCTYPE html>
<html lang="en">
<head>
<meta charset="utf-8">
<title>Brewvale Assam Tea – Pouch Labels</title>
<link href="https://fonts.googleapis.com/css2?family=Josefin+Sans:wght@300;400;600&family=Lato:wght@400;700&display=swap" rel="stylesheet">
<style>
  :root {
    --pouch-green: #0e5b4c;
    --pouch-green-light: #146a59;
    --gold: #c9a24c;
    --white: #ffffff;
    --ink: #1b1b1b;
    --stage: #eef0ec;
  }
  * { box-sizing: border-box; margin: 0; padding: 0; }
  html, body { width: 1200px; height: 900px; overflow: hidden; }
  body {
    background: var(--stage);
    font-family: "Lato", sans-serif;
    color: var(--white);
    position: relative;
  }
  .label {
    position: absolute;
    top: 110px;
    width: 480px;
    height: 680px;
    background: linear-gradient(160deg, var(--pouch-green-light), var(--pouch-green) 60%);
    border-radius: 6px;
  }
  .label--front { left: 90px; }
  .label--rear { left: 630px; padding: 28px 26px; }

  /* Front */
  .brand {
    position: absolute;
    top: 160px; left: 0; right: 0;
    text-align: center;
  }
  .brand__mark {
    width: 74px; height: 74px;
    border: 3px solid var(--gold);
    border-radius: 50%;
    margin: 0 auto 26px;
  }
  .brand__name {
    font-family: "Josefin Sans", sans-serif;
    font-weight: 300;
    font-size: 64px;
    letter-spacing: 10px;
    color: var(--gold);
  }
  .tagline-art {
    position: absolute;
    top: 365px; left: 110px;
    width: 260px; height: 50px;
    border-radius: 6px;
    background: linear-gradient(90deg, rgba(201,162,76,0.25), rgba(201,162,76,0.4), rgba(201,162,76,0.25));
  }
  .origin {
    position: absolute;
    left: 110px; bottom: 70px;
    display: flex; align-items: center; gap: 16px;
  }
  .origin__badge {
    width: 72px; height: 72px;
    border-radius: 50%;
    border: 2px solid var(--gold);
    background: rgba(201,162,76,0.25);
  }
  .origin__divider { width: 2px; height: 68px; background: var(--gold); }
  .origin__text {
    font-family: "Josefin Sans", sans-serif;
    color: var(--gold);
    font-weight: 600;
    line-height: 1.35;
  }
  .origin__percent { font-size: 22px; }
  .origin__kind, .origin__weight { font-size: 13px; letter-spacing: 0.5px; }
  .origin__weight { margin-top: 8px; }

  /* Rear */
  .rear__title {
    font-family: "Josefin Sans", sans-serif;
    font-weight: 600;
    font-size: 15px;
    text-align: center;
    margin-top: 110px;
    margin-bottom: 16px;
  }
  .rear__columns { display: flex; gap: 18px; }
  .rear__story { flex: 1; font-size: 8.6px; line-height: 1.32; }
  .rear__story p { margin-bottom: 8px; }
  .rear__story h3, .rear__info h3 {
    font-family: "Josefin Sans", sans-serif;
    font-size: 9.5px; font-weight: 600;
    color: var(--gold);
    margin: 6px 0 2px;
    text-transform: uppercase;
  }
  .rear__story ul { list-style: none; }
  .rear__story li::before { content: "• "; }
  .rear__side { width: 196px; }

  .nutrition {
    background: var(--white);
    color: var(--ink);
    border: 3px solid var(--gold);
    outline: 2px solid var(--white);
    outline-offset: 2px;
    border-radius: 8px;
    padding: 8px 9px;
    font-size: 8px;
  }
  .nutrition__title {
    font-family: "Josefin Sans", sans-serif;
    font-size: 15px; font-weight: 600;
    border-bottom: 1px solid var(--ink);
    padding-bottom: 3px; margin-bottom: 3px;
  }
  .nutrition table { width: 100%; border-collapse: collapse; }
  .nutrition td { padding: 2px 0; border-bottom: 1px solid #999; }
  .nutrition td:last-child { text-align: right; }
  .nutrition thead td { border-bottom: 2px solid var(--ink); font-size: 7.5px; }
  .nutrition .indent { padding-left: 14px; }
  .nutrition__note { margin-top: 6px; font-size: 8px; }

  .rear__info { font-size: 8.4px; line-height: 1.32; margin-top: 14px; }
  .rear__info p { margin-bottom: 7px; }

  .rear__contact {
    text-align: center;
    font-size: 8.6px;
    line-height: 1.4;
    margin-top: 16px;
  }
  .sticker {
    margin: 12px 0 0 18px;
    width: 170px;
    background: var(--white);
    color: var(--ink);
    border-radius: 10px;
    padding: 8px 10px;
    font-size: 7.6px;
    line-height: 1.3;
    text-align: center;
  }
</style>
</head>
<body>

<section class="label label--front" aria-label="Front label">
  <div class="brand">
    <div class="brand__mark"></div>
    <div class="brand__name">BREWVALE</div>
  </div>
  <div class="tagline-art" role="img" aria-label="Hand-lettered tagline: freshest possible"></div>
  <div class="origin">
    <div class="origin__badge" role="img" aria-label="Origin certification badge"></div>
    <div class="origin__divider"></div>
    <div class="origin__text">
      <div class="origin__percent">100%</div>
      <div class="origin__kind">Single Estate Tea</div>
      <div class="origin__weight">Net Wt 250g/8.82oz</div>
    </div>
  </div>
</section>

<section class="label label--rear" aria-label="Rear label">
  <h2 class="rear__title">TEA LOSES ITS FLAVOUR AND AROMA OVER TIME</h2>
  <div class="rear__columns">
    <div class="rear__story">
      <p>This tea tastes good for 24 months after being processed in the factory. Most tea that you get passes through multiple middlemen – auction house, wholesaler, local exporter and takes between 6–12 months after harvest to reach you. By then tea has already lost a lot of its flavour and aroma.</p>
      <p>We come from a family of small-scale tea growers in Assam, India and will source tea directly from our own tea estates or from similar estates like us. Hence, we are able to tell you when the tea was picked from the garden and when it was packed. By sourcing tea directly from small-scale tea estates, we are removing middlemen, giving a better price to the tea growers and reducing the time it takes to reach tea lovers like yourself.</p>
      <h3>What does it taste like?</h3>
      <ul><li>Strong, malty, astringent taste and aroma</li></ul>
      <h3>How do I drink it?</h3>
      <ul>
        <li>Rinse the teapot or cup with boiling water</li>
        <li>Add 2 teaspoon (~2 g) of tea leaves into the teapot and then pour boiling water and cover it with the lid</li>
        <li>Allow the tea to brew for one minute. Keep it longer for around three minutes for a stronger brew</li>
        <li>Pour the brew into a cup using a strainer</li>
        <li>Add milk and sugar to taste</li>
      </ul>
    </div>
    <div class="rear__side">
      <div class="nutrition">
        <div class="nutrition__title">NUTRITIONAL FACTS</div>
        <table>
          <thead><tr><td>Typical Values</td><td>Per 100ml Brewed Infusion*</td></tr></thead>
          <tbody>
            <tr><td>Energy</td><td>&lt;4 kcal</td></tr>
            <tr><td>Fat</td><td>0 g</td></tr>
            <tr><td class="indent">Of which saturates</td><td>0 g</td></tr>
            <tr><td>Carbohydrates</td><td>0 g</td></tr>
            <tr><td class="indent">Of which sugar</td><td>0 g</td></tr>
            <tr><td>Protein</td><td>&lt;0.5 g</td></tr>
            <tr><td>Salt</td><td>0 g</td></tr>
          </tbody>
        </table>
        <p class="nutrition__note">*Based on an infusion brewed with 200ml water for 3 minutes.</p>
      </div>
      <div class="rear__info">
        <h3>Ingredients: Black Tea</h3>
        <p>Allergen information: Made in a factory that processes nuts.</p>
        <h3>How do I store it:</h3>
        <p>Store in an airtight container made of ceramic or tin to keep the light out</p>
        <p>Packed in the UK<br>by Brewvale Limited,<br>14 Orchard Row, Reading, RG1 4QT, United Kingdom</p>
      </div>
    </div>
  </div>
  <div class="rear__contact">
    Visit our website at www.brewvale.co.uk<br>
    Write to us at hello@brewvale.co.uk or Brewvale Limited, 14 Orchard Row,<br>
    Reading, RG1 4QT, United Kingdom
  </div>
  <div class="sticker">
    "Blank space for sticker"<br>
    Picked on: September 2019<br>
    Packaged on: May 2020<br>
    Best before: May 2022<br>
    Tea type: Black Tea BOP<br>
    Batch no. LOT/12345ABC
  </div>
</section>

</body>
</html>
```